Business Card Design for Vintage Jazz

I am a vintage jazz band leader in New York City. My groups play the music of the 1920s, 1930s and 1940s. My website is morvalquist.com for more info on what I do.

I am looking for a two sided business card design that has the look and feel of a really nice business card from the 1930s. I need to convey with the design that my work has that vintage kind of class and style, but also conveys that we are fun and entertaining.

Most importantly it should make a bold staement. If Hal Denbrook had a card, what would it have looked like? I want a card that I feel confident will make an impact and will let people know that my work is te the top that NYC has to offer in vintage jazz..

Note that I have only decided to avoid the "committed payment" option as I have not used this service before. Assuming that I get quality work I will select a design from those presented.

Target Market(s)

people who want to hire my band for events, media, and new fans of the band

Industry/Entity Type

Performing Art

Contact Information for Business Card

Definitely a matte finish, possibly a sort of old style of paper with that brown tint? definitely a thick card.

Requirements
Must have
• FRONT
• My name: Tobin Vashley
• What I do: Bandleader, Guitarist, Vocalist, Songwriter
• Contact Details: morvalquist.com tobin@morvalquist.com 646-555-0148
• BACK
• My Social Media Links:
• facebook.morvalquist.com
• twitter, instagram, linkedin: morvalquist
• I'm also including a photo image I would like to use. The photo's background is not needed, and to be honest isn't really desireable. Just looking to use the image of me.
Nice to have
• I'm attaching which could be used as is, omitted from the card, or altered maybe with text going around the outside of the circle or in some other way. It may need some clean up to the edges of the lettering as we only use it for the website thumbnail.
• If there's space I'd like to include the text "join our mailing list for a free song download: freesong.morvalquist.com" If not perhaps just "Download a Free Song at: freesong.morvalquist.com - something to this end.
Should not have
• anything cartoony. Don't think retro 90s's vision of the swing era, think actual swing era!
• anything modern. Got to look old school
• Try to avoid dark backgrounds. Since we often play in bars and clubs where it is dar, a d
• avoid script fonts.

```html
<!DOCTYPE html>
<html lang="en">
<head>
<meta charset="utf-8">
<title>Tobin Vashley – Business Card</title>
<link href="https://fonts.googleapis.com/css2?family=Ubuntu:wght@400;500;700&family=Open+Sans:wght@400;600&display=swap" rel="stylesheet">
<style>
  :root {
    --teal: #5bb8a4;
    --teal-deep: #4aa892;
    --ink: #2b2b2b;
    --grey-text: #5a5a5a;
    --card: #f4f4f2;
    --backdrop: #dcdcdc;
  }
  * { box-sizing: border-box; margin: 0; padding: 0; }
  html, body { width: 1200px; height: 795px; overflow: hidden; }
  body {
    background: var(--backdrop);
    font-family: "Open Sans", sans-serif;
    position: relative;
  }
  .card {
    position: absolute;
    top: 237px;
    width: 540px;
    height: 320px;
    background: var(--card);
    border-radius: 18px;
    box-shadow: 0 6px 18px rgba(0,0,0,.18);
    overflow: hidden;
  }
  .card--front { left: 40px; }
  .card--back { left: 620px; }

  /* front */
  .portrait {
    position: absolute;
    left: 36px; top: 90px;
    width: 210px; height: 210px;
    border-radius: 50%;
    background: radial-gradient(circle at 55% 45%, #6a6a6a 0 38%, var(--teal) 39%);
  }
  .front-text {
    position: absolute;
    left: 250px; top: 40px;
    width: 270px;
  }
  .name {
    font-family: "Ubuntu", sans-serif;
    font-weight: 700;
    color: var(--teal);
    font-size: 40px;
    line-height: 1;
    white-space: nowrap;
  }
  .role {
    margin-top: 8px;
    font-size: 12.5px;
    color: var(--grey-text);
    white-space: nowrap;
  }
  .social {
    display: flex;
    gap: 8px;
    margin-top: 14px;
  }
  .social span {
    width: 17px; height: 17px;
    border-radius: 50%;
    background: var(--teal);
  }
  .site {
    margin-top: 14px;
    font-size: 14px;
    letter-spacing: 2.5px;
    color: var(--grey-text);
  }
  .site b { color: var(--ink); font-weight: 600; }

  /* back */
  .monogram {
    position: absolute;
    left: 40px; top: 100px;
    width: 170px; height: 170px;
    border-radius: 50%;
    background: var(--teal);
    display: flex; align-items: center; justify-content: center;
    font-family: "Ubuntu", sans-serif;
    font-weight: 700;
    font-size: 66px;
    color: var(--ink);
  }
  .back-text {
    position: absolute;
    left: 265px; top: 50px;
  }
  .back-text .name { font-size: 28px; font-weight: 500; }
  .contacts {
    list-style: none;
    margin-top: 22px;
  }
  .contacts li {
    display: flex; align-items: center; gap: 8px;
    font-size: 13px;
    color: var(--ink);
    line-height: 1.55;
  }
  .contacts svg { width: 12px; height: 12px; flex: none; }
  .tagline {
    position: absolute;
    left: 40px; right: 30px; bottom: 34px;
    text-align: right;
    font-size: 15px;
    letter-spacing: 1px;
    color: var(--grey-text);
  }
</style>
</head>
<body>
  <section class="card card--front">
    <div class="portrait" role="img" aria-label="Black and white photo of the bandleader in a striped blazer tipping a straw boater hat, on a teal circle"></div>
    <div class="front-text">
      <h1 class="name">Tobin Vashley</h1>
      <p class="role">Bandleader, Guitarist, Vocalist, Songwriter</p>
      <div class="social" aria-label="Social media links">
        <span></span><span></span><span></span><span></span><span></span><span></span><span></span><span></span>
      </div>
      <p class="site">www.<b>morvalquist</b>.com</p>
    </div>
  </section>

  <section class="card card--back">
    <div class="monogram">TV</div>
    <div class="back-text">
      <h2 class="name">Tobin Vashley</h2>
      <ul class="contacts">
        <li><svg viewBox="0 0 12 12"><circle cx="6" cy="6" r="6" fill="#5bb8a4"/><path d="M4 3.2l1.2 1.3-.6.8c.4.9 1.1 1.6 2 2l.8-.6L8.8 8 8 8.9C5.6 8.6 3.4 6.4 3.1 4z" fill="#fff"/></svg>646-555-0148</li>
        <li><svg viewBox="0 0 12 12"><circle cx="6" cy="6" r="6" fill="#5bb8a4"/><rect x="3" y="4" width="6" height="4.2" fill="none" stroke="#fff" stroke-width=".9"/><path d="M3 4l3 2.3L9 4" fill="none" stroke="#fff" stroke-width=".9"/></svg>tobin@morvalquist.com</li>
        <li><svg viewBox="0 0 12 12"><circle cx="6" cy="6" r="6" fill="#5bb8a4"/><circle cx="6" cy="6" r="3.2" fill="none" stroke="#fff" stroke-width=".8"/><path d="M2.8 6h6.4M6 2.8v6.4" stroke="#fff" stroke-width=".8"/></svg>www.morvalquist.com</li>
      </ul>
    </div>
    <p class="tagline">BANDLEADER, GUITARIST, VOCALIST, SONGWRITER</p>
  </section>
</body>
</html>
```